HarvestelloPL Business Card Design - Opaque White Plastic

The design Include "Company Logo" + "QR Code"
While designing this business card, please be noted that agribusiness are the company's industry and it is important that your final design take this into consideration

We hope that you could design a business card that could be printed in Opaque White Plastic - http://www.quillpressa.com/product2/card.php?acode=75

 Each document is set to CMYK
 Each document is at least 300dpi
 Make sure all your text is converted to outlines
 Make sure all your text is "NOT" printed in white ink
 Make sure each document is set to the right size (plastic document size= 3.54” x 2.28”)
 Make sure that it is a template that enables user to change the detail on the design easily

****Finally design must be a template format that could be uploaded to http://www.quillpressa.com/product2/card.php?acode=75
and editable for multiple person

Target Market(s)

Agribusiness

Industry/Entity Type

Agribusiness

Contact Information for Business Card

Font styles to use
Serif
Sans Serif

Requirements
Must have
• Company Logo
• QR Code
Nice to have
• Would love to see Design that are concise but modern

```html
<!DOCTYPE html>
<html lang="en">
<head>
<meta charset="UTF-8">
<title>HarvestelloPL Business Card</title>
<link rel="stylesheet" href="https://fonts.googleapis.com/css2?family=Source+Sans+3:wght@400;600&display=swap">
<style>
  :root {
    --page-bg: #e9e8e5;
    --card-bg: #fbfaf8;
    --card-edge: #d9d6d1;
    --ink: #2f2f2f;
    --ink-soft: #444444;
    --brand-green: #5a9a2e;
    --brand-lime: #9cc63c;
    --brand-blue: #2a7fc0;
    --brand-navy: #1f4f9a;
    --icon-blue: #1f4f8a;
  }
  * { margin: 0; padding: 0; box-sizing: border-box; }
  html, body {
    width: 1200px;
    height: 970px;
    overflow: hidden;
    background: var(--page-bg);
    font-family: "Source Sans 3", sans-serif;
  }
  .business-card {
    position: absolute;
    left: 100px;
    top: 207px;
    width: 1000px;
    height: 556px;
    overflow: hidden;
    background: linear-gradient(135deg, #ffffff 0%, var(--card-bg) 60%, #f3f1ee 100%);
    border: 1px solid var(--card-edge);
    box-shadow: 0 6px 20px rgba(0,0,0,0.12);
  }
  .brand-graphic {
    position: absolute;
    right: 0;
    top: 0;
    width: 310px;
    height: 100%;
    background: linear-gradient(160deg, var(--brand-lime) 0%, var(--brand-blue) 40%, var(--brand-green) 70%, var(--brand-navy) 100%);
    opacity: 0.85;
  }
  .brand {
    position: absolute;
    left: 50px;
    top: 167px;
    display: flex;
    align-items: center;
    gap: 14px;
  }
  .brand-dot {
    width: 34px;
    height: 34px;
    border-radius: 50%;
    background: var(--brand-green);
  }
  .brand-name {
    font-size: 34px;
    font-weight: 600;
    color: var(--ink-soft);
    letter-spacing: 0.5px;
  }
  .holder-name {
    position: absolute;
    left: 50px;
    top: 282px;
    font-size: 42px;
    font-weight: 400;
    color: var(--ink);
  }
  .holder-title {
    position: absolute;
    left: 52px;
    top: 340px;
    font-size: 24px;
    color: var(--brand-green);
  }
  .contact-list {
    position: absolute;
    left: 52px;
    top: 394px;
    list-style: none;
  }
  .contact-item {
    display: flex;
    align-items: center;
    height: 45px;
    font-size: 25px;
    font-weight: 600;
    color: var(--ink);
  }
  .contact-icon {
    width: 28px;
    height: 24px;
    margin-right: 17px;
    fill: var(--icon-blue);
  }
</style>
</head>
<body>
  <main class="business-card">
    <div class="brand-graphic" role="img" aria-label="Large company emblem decoration in blue and green"></div>

    <div class="brand">
      <span class="brand-dot"></span>
      <span class="brand-name">HarvestelloPL</span>
    </div>

    <h1 class="holder-name">Your Name</h1>
    <p class="holder-title">Job Title</p>

    <ul class="contact-list">
      <li class="contact-item">
        <svg class="contact-icon" viewBox="0 0 28 24" aria-hidden="true">
          <rect x="2" y="5" width="24" height="15"/>
          <polyline points="2,5 14,14 26,5" fill="none" stroke="#fff" stroke-width="2"/>
        </svg>
        youremail@xyz.com
      </li>
      <li class="contact-item">
        <svg class="contact-icon" viewBox="0 0 28 24" aria-hidden="true">
          <rect x="8" y="1" width="12" height="22" rx="2"/>
          <rect x="10" y="4" width="8" height="13" fill="#fff"/>
          <circle cx="14" cy="20" r="1.3" fill="#fff"/>
        </svg>
        000 000 0000
      </li>
      <li class="contact-item">
        <svg class="contact-icon" viewBox="0 0 28 24" aria-hidden="true">
          <path d="M2 9 Q14 0 26 9 L22 11 L19 7 Q14 5 9 7 L6 11 Z"/>
          <rect x="5" y="12" width="18" height="10" rx="2"/>
          <circle cx="14" cy="17" r="2.5" fill="#fff"/>
        </svg>
        000 000 0000
      </li>
    </ul>
  </main>
</body>
</html>
```